New business card for a regional office of a US M&A company

We need business card for a finance company, office based in Hong Kong , our Head office is in US, our business is to Merge and acquires companies , the new office will be a regional office for the Asia Pacific region. We want to use the head office logo as attached ( but don't have to be exactly the same, can be a variation to it) as a base and then add Asia Pacific alongside the logo.
We would prefer to have be bilingual Eng + Chinese, although we don't really have Chinese company name .

Industry/Entity Type

Business

Contact Information for Business Card

Clara Jo Tsang
 

VP,
APAC M&A Operations
ORIN VANTAGE Asia Pacific Limited
 
Unit 1407, K18
18 Tai Lok Shan Road, 
Hong Kong 
 
M: +852 6038 1742
T : +852 2836 4100
F : +852 2836 4177
VOIP: 4158
 
cjtsang@orinvantage.com

Font styles to use
Serif
Sans Serif

Colors

Designer to choose colors to be used in the design.

Requirements
Must have
• APAC Office

```html
<!DOCTYPE html>
<html lang="en">
<head>
<meta charset="utf-8">
<title>Orin Vantage Asia Pacific – Business Card</title>
<link rel="stylesheet" href="https://fonts.googleapis.com/css2?family=Montserrat:wght@400;500;700&family=Tinos&display=swap">
<style>
  :root {
    --stage: #3a3b3e;
    --navy: #0d2a47;
    --navy-deep: #0a2038;
    --cyan: #1aa3c9;
    --paper: #f3f3f3;
    --ink: #4a4a4a;
    --map: #e2e3e5;
  }
  * { box-sizing: border-box; margin: 0; padding: 0; }
  html, body { width: 1200px; height: 834px; overflow: hidden; }
  body {
    background: var(--stage);
    display: flex;
    align-items: center;
    justify-content: center;
    gap: 40px;
    font-family: "Montserrat", sans-serif;
  }
  .card {
    width: 520px;
    height: 300px;
    position: relative;
    overflow: hidden;
    box-shadow: 0 10px 24px rgba(0,0,0,.35);
  }
  /* front */
  .card--front {
    background: radial-gradient(circle at 60% 40%, var(--navy) 0%, var(--navy-deep) 100%);
    display: flex;
    flex-direction: column;
    align-items: center;
    justify-content: center;
  }
  .brand-square {
    width: 28px;
    height: 28px;
    background: #d7dbe0;
    margin-bottom: 12px;
  }
  .brand-name {
    color: var(--cyan);
    font-weight: 700;
    font-size: 22px;
    letter-spacing: 1px;
    padding-bottom: 8px;
    border-bottom: 2px solid var(--cyan);
  }
  /* back */
  .card--back { background: linear-gradient(135deg, #fafafa 0%, #e9e9e9 100%); }
  .brand-block {
    position: absolute;
    left: 56px;
    top: 118px;
    width: 190px;
    height: 108px;
    background: var(--navy);
    border-bottom: 4px solid var(--cyan);
    display: flex;
    flex-direction: column;
    align-items: center;
    justify-content: center;
  }
  .brand-block .brand-square { width: 22px; height: 22px; margin-bottom: 10px; }
  .brand-block .brand-name { font-size: 17px; border: 0; padding: 0; }
  .map-area {
    position: absolute;
    left: 90px;
    bottom: 0;
    width: 430px;
    height: 120px;
    background: linear-gradient(180deg, rgba(226,227,229,0) 0%, var(--map) 100%);
  }
  .contact {
    position: absolute;
    left: 286px;
    top: 40px;
    color: var(--ink);
    font-size: 10.5px;
    line-height: 1.4;
  }
  .contact__name { font-family: "Tinos", serif; font-size: 17px; color: #333; }
  .contact__title { color: var(--cyan); font-size: 11px; margin-bottom: 12px; }
  .contact__company { color: var(--cyan); font-weight: 700; }
  .contact__address { margin-bottom: 12px; }
  .contact__phones li { list-style: none; display: flex; align-items: center; gap: 6px; }
  .contact__phones svg { width: 9px; height: 9px; flex: none; }
  .contact__phones .voip { padding-left: 15px; margin-top: 2px; }
</style>
</head>
<body>
  <section class="card card--front">
    <div class="brand-square"></div>
    <div class="brand-name">ORIN VANTAGE</div>
  </section>

  <section class="card card--back">
    <div class="map-area" role="img" aria-label="Faint dotted map of the Asia Pacific region"></div>
    <div class="brand-block">
      <div class="brand-square"></div>
      <div class="brand-name">ORIN VANTAGE</div>
    </div>
    <div class="contact">
      <p class="contact__name">Clara Jo Tsang</p>
      <p class="contact__title">VP, APAC M&amp;A Operations</p>
      <p class="contact__company">Orin Vantage Asia Pacific Limited</p>
      <p class="contact__address">Unit 1407, K18<br>18 Tai Lok Shan Road,<br>Hong Kong</p>
      <ul class="contact__phones">
        <li><svg viewBox="0 0 10 10"><rect x="2.5" y="0.5" width="5" height="9" rx="1" fill="none" stroke="#1aa3c9"/></svg>+852 6038 1742</li>
        <li><svg viewBox="0 0 10 10"><path d="M2 1l2 2-1 1.2c.8 1.4 1.5 2.1 2.8 2.8L7 6l2 2-1.3 1.3C4.5 9 1 5.5.7 2.3z" fill="#1aa3c9"/></svg>+852 2836 4100</li>
        <li><svg viewBox="0 0 10 10"><rect x="1" y="4" width="8" height="5" rx="1" fill="#1aa3c9"/><rect x="2.5" y="1" width="5" height="3" fill="none" stroke="#1aa3c9"/></svg>+852 2836 4177</li>
        <li class="voip">VOIP 4158</li>
      </ul>
    </div>
  </section>
</body>
</html>
```